Northvale Strategy Partners Website Design

I need a website design for my new business consulting and executive coaching firm, Northvale Strategy Partners. We provide consultative services to business C-suites as well as personal coaching to executives. I have attached the logo with color scheme I have chosen. I would like the website to reflect professionalism and continue the color scheme in the logo.

Target Market(s)

Small to medium business and their executives; middle to upper income men and women in mid- to late career looking for significance

Industry/Entity Type

Business Consultant

Number of Pages Required

4 page

Requirements
Must have
• A homepage with prominent logo and way to contact for more information; an area on the homepage with easy to read, clear text to describe what the company does; a prominent area on the homepage for a tagline; a blog page that can be updated regularly, an "about us" page with biographical information; an "about us" page; a page detailing services offered
• The web design must match the logo colors and font that I have uploaded.
Nice to have
• A lighthouse picture in the background or header
Should not have
• A lot of text area on the homepage

```html
<!DOCTYPE html>
<html lang="en">
<head>
<meta charset="utf-8">
<title>Northvale Strategy Partners</title>
<link href="https://fonts.googleapis.com/css2?family=Roboto+Slab:wght@400&family=Roboto+Condensed:wght@400&family=Arimo:wght@400;700&display=swap" rel="stylesheet">
<style>
:root{
  --navy:#1d2b63;
  --navy-deep:#172352;
  --maroon:#7a1414;
  --white:#ffffff;
  --grey-text:#666666;
  --grey-title:#555555;
  --grey-button:#6b6b6b;
  --ring:#d6d6d6;
  --footer:#383838;
  --footer-edge:#7a1111;
  --sky-top:#b06aae;
  --sky-mid:#d8788f;
  --sky-low:#d97a5a;
}
*{margin:0;padding:0;box-sizing:border-box}
html,body{width:1200px;height:939px;overflow:hidden;background:var(--footer)}
.page{position:relative;width:1200px;height:939px;overflow:hidden;font-family:"Arimo",Arial,sans-serif}

.hero-scene{
  position:absolute;left:0;top:0;width:1200px;height:780px;
  background:linear-gradient(180deg,var(--sky-top) 0%,var(--sky-mid) 45%,var(--sky-low) 100%);
}

.brand{position:absolute;left:163px;top:80px;display:flex;align-items:center;gap:10px}
.brand-mark{width:26px;height:26px;background:var(--maroon)}
.brand-name{font-family:"Roboto Slab",Georgia,serif;font-size:18px;line-height:21px;color:var(--navy);letter-spacing:.5px;text-transform:uppercase}

.contact-phone{position:absolute;left:879px;top:6px;display:flex;align-items:center;gap:14px;color:var(--white);font-family:"Roboto Condensed",Arial,sans-serif;font-size:20px;letter-spacing:.5px}
.contact-phone svg{width:30px;height:30px}

.main-nav{position:absolute;top:51px;left:579px;display:flex;align-items:center}
.main-nav a{font-family:"Roboto Slab",Georgia,serif;font-size:14.5px;color:var(--white);text-decoration:none;height:24px;line-height:24px;padding:0 13px;margin-right:9px;text-transform:uppercase}
.main-nav a.is-active{background:var(--navy);width:68px;text-align:center;padding:0}
.main-nav a:nth-child(2){margin-left:19px}

.tagline{position:absolute;left:160px;top:245px;width:620px;font-family:"Roboto Slab",Georgia,serif;font-weight:400;font-size:31.5px;line-height:37px;color:var(--navy);white-space:nowrap}

.footer-band{position:absolute;left:0;top:780px;width:1200px;height:153px;background:var(--footer)}
.footer-edge{position:absolute;left:0;top:933px;width:1200px;height:6px;background:var(--footer-edge)}

.feature-card{position:absolute;top:636px;width:273px;height:191px;background:var(--white);text-align:center;border:1px solid #e4e4e4}
.feature-card.about{left:160px}
.feature-card.services{left:464px}
.feature-card.inquiry{left:767px}
.feature-icon{position:absolute;left:50%;top:-76px;width:120px;height:120px;margin-left:-60px;border-radius:50%;border:4px solid var(--ring);display:flex;align-items:center;justify-content:center;box-shadow:0 2px 4px rgba(0,0,0,.25)}
.feature-icon.maroon{background:var(--maroon);border-color:var(--navy)}
.feature-icon.navy{background:var(--navy)}
.feature-title{margin-top:52px;font-family:"Roboto Condensed",Arial,sans-serif;font-size:20.5px;color:var(--grey-title);font-weight:400}
.feature-card.about .feature-title{color:var(--navy)}
.feature-card.inquiry .feature-title{text-transform:uppercase}
.feature-text{margin:8px auto 0;width:248px;font-size:11.6px;line-height:18.5px;color:var(--grey-text)}
.feature-button{position:absolute;left:50%;top:145px;width:105px;height:31px;padding-left:9px;display:flex;align-items:center;font-size:13px;color:var(--white);text-transform:uppercase;text-decoration:none;white-space:nowrap;background:var(--grey-button);clip-path:polygon(0 0,calc(100% - 14px) 0,100% 50%,calc(100% - 14px) 100%,0 100%)}
.feature-button.primary{background:var(--navy-deep)}
.feature-card.about .feature-button{margin-left:-52px}
.feature-card.services .feature-button{margin-left:-47px}
.feature-card.inquiry .feature-button{margin-left:-56px;width:116px}

.social{position:absolute;left:0;top:859px;width:1200px;display:flex;justify-content:center;align-items:center;gap:6px;padding-left:2px}
.social-label{font-family:"Roboto Condensed",Arial,sans-serif;font-size:16px;color:var(--white);margin-right:6px}
.social-dot{width:28px;height:28px;border-radius:50%;background:var(--white)}
.copyright{position:absolute;left:0;top:898px;width:1200px;text-align:center;font-size:12.8px;color:var(--white)}
</style>
</head>
<body>
<div class="page">
  <div class="hero-scene" role="img" aria-label="Photograph of a lighthouse on a rocky shore at sunset, its beam crossing a purple and orange sky above the sea"></div>

  <div class="brand">
    <span class="brand-mark"></span>
    <span class="brand-name">Northvale<br>Strategy Partners</span>
  </div>

  <div class="contact-phone">
    <svg viewBox="0 0 30 30" aria-hidden="true">
      <circle cx="15" cy="15" r="13.5" fill="none" stroke="#fff" stroke-width="2"/>
      <path d="M11 8.5c1-.6 1.6-.4 2 .3l1.2 2.4c.3.6.1 1.1-.4 1.5l-.9.7c.4 1.6 1.5 3.4 2.9 4.6l1-.6c.5-.3 1.1-.2 1.5.3l1.5 2c.4.6.3 1.3-.4 1.8-1.4 1-3.1.9-4.6-.3-2.5-2-4.4-5-5-8.1-.3-1.7.2-3.6 1.2-4.6z" fill="#fff"/>
    </svg>
    <span>123-456-7890</span>
  </div>

  <nav class="main-nav">
    <a class="is-active" href="#">Home</a>
    <a href="#">About Us</a>
    <a href="#">Services</a>
    <a href="#">Blog</a>
    <a href="#">Contact Us</a>
  </nav>

  <h1 class="tagline">We Are A Firm&nbsp; Providing Business<br>Consulting And Executive<br>Coaching</h1>

  <div class="footer-band"></div>
  <div class="footer-edge"></div>

  <section class="feature-card about">
    <div class="feature-icon maroon"></div>
    <h2 class="feature-title">About Us</h2>
    <p class="feature-text">Lorem ipsum dolor sit amet, consectetuer into euismod tincidunt ut laoreet dolore magnain aliquam erat volutpat.</p>
    <a class="feature-button primary" href="#">Read More</a>
  </section>

  <section class="feature-card services">
    <div class="feature-icon navy">
      <svg width="58" height="54" viewBox="0 0 58 54" aria-hidden="true">
        <rect x="8" y="4" width="42" height="30" rx="3" fill="none" stroke="#fff" stroke-width="2.5"/>
        <rect x="16" y="22" width="5" height="7" fill="#fff"/>
        <rect x="25" y="16" width="5" height="13" fill="#fff"/>
        <rect x="34" y="11" width="5" height="18" fill="#fff"/>
        <line x1="29" y1="34" x2="29" y2="46" stroke="#fff" stroke-width="2.5"/>
        <line x1="20" y1="50" x2="38" y2="50" stroke="#fff" stroke-width="2.5"/>
      </svg>
    </div>
    <h2 class="feature-title">Services We Provide</h2>
    <p class="feature-text">Lorem ipsum dolor sit amet, consectetuer into euismod tincidunt ut laoreet dolore magnain aliquam erat volutpat.</p>
    <a class="feature-button" href="#">Read More</a>
  </section>

  <section class="feature-card inquiry">
    <div class="feature-icon navy">
      <svg width="62" height="62" viewBox="0 0 30 30" aria-hidden="true">
        <circle cx="15" cy="15" r="13.5" fill="none" stroke="#fff" stroke-width="1.4"/>
        <path d="M11 8.5c1-.6 1.6-.4 2 .3l1.2 2.4c.3.6.1 1.1-.4 1.5l-.9.7c.4 1.6 1.5 3.4 2.9 4.6l1-.6c.5-.3 1.1-.2 1.5.3l1.5 2c.4.6.3 1.3-.4 1.8-1.4 1-3.1.9-4.6-.3-2.5-2-4.4-5-5-8.1-.3-1.7.2-3.6 1.2-4.6z" fill="none" stroke="#fff" stroke-width="1.2"/>
      </svg>
    </div>
    <h2 class="feature-title">Quick Inquiry</h2>
    <p class="feature-text">Lorem ipsum dolor sit amet, consectetuer into euismod tincidunt ut laoreet dolore magnain aliquam erat volutpat.</p>
    <a class="feature-button" href="#">Get Started</a>
  </section>

  <div class="social">
    <span class="social-label">FOLLOW US</span>
    <span class="social-dot" aria-label="Social profile"></span>
    <span class="social-dot" aria-label="Social profile"></span>
    <span class="social-dot" aria-label="Social profile"></span>
    <span class="social-dot" aria-label="Social profile"></span>
  </div>
  <p class="copyright">© 2016 Northvale Strategy Partners All Rights Reserved</p>
</div>
</body>
</html>
```